Real estate business card

I need a business card for my real estate company. I help clients buy and sell properties. I would like to keep the design very simple and professional. I would like the design to convey professionalism, safety and trust. I prefer no graphics but a simple logo design would be nice if that is part of what you do.
Updates

Please keep the designs simple. No high-rise buildings please. 

Project Deadline Extended
Reason: My design has not been finalized.

Target Market(s)

Age group 30-60 mostly affluent

Industry/Entity Type

Real Estate

Contact Information for Business Card

Velmont Realtors
Gregory Velmont, Broker
4815 Brindle Ave. #263, La Crescenta, CA 91206

Requirements
Nice to have
• Logo can be combination of my initials GV or just Z or a simple geometric shape? Please see "Desig Ideas" attachment. No pics of houses or shaking hands, dollar bills, $, %, etc...
Please use fonts similar to Helvetica for a clean, modern look (think Northern European design, simple, clean yet bold)

Also use font colors such as blue, grey in different shades. Use pastel colors if better.

```html
<!DOCTYPE html>
<html lang="en">
<head>
<meta charset="utf-8">
<title>Velmont Realtors – Business Card</title>
<link rel="stylesheet" href="https://fonts.googleapis.com/css2?family=Exo+2:wght@400;500;600&display=swap">
<style>
  :root {
    --backdrop: #2c2e31;
    --card: #ffffff;
    --ink: #2a2a2c;
    --ink-soft: #4a4d52;
    --band-dark: #232325;
    --band-mid: #3a3b3e;
    --divider: #5a5c60;
    --blue-deep: #2f5fb8;
    --blue: #3f7fd0;
    --cyan: #5cc3d8;
    --icon-light: #6fb2ea;
    --white: #ffffff;
  }
  * { box-sizing: border-box; margin: 0; padding: 0; }
  html, body {
    width: 1200px; height: 817px; overflow: hidden;
    background: var(--backdrop);
    font-family: "Exo 2", sans-serif;
  }
  .card {
    position: absolute; left: 150px; top: 151px;
    width: 900px; height: 514px;
    background: var(--card);
    border-radius: 42px;
    overflow: hidden;
  }
  .brand {
    position: absolute; left: 60px; top: 78px;
    display: flex; align-items: center; gap: 18px;
  }
  .brand-mark {
    width: 44px; height: 44px; border-radius: 50%;
    background: var(--blue);
  }
  .brand-name {
    font-size: 36px; font-weight: 500; letter-spacing: 2px;
    color: var(--ink); text-transform: uppercase;
  }
  .name-band {
    position: absolute; left: 0; top: 188px;
    width: 100%; height: 58px;
    background: linear-gradient(90deg, var(--band-dark), var(--band-mid) 60%, var(--band-dark));
    display: flex; align-items: center;
    padding-left: 110px;
    color: var(--white);
  }
  .person-icon {
    position: absolute; left: 40px; top: 6px; width: 46px; height: 46px;
  }
  .person-name {
    font-size: 30px; font-weight: 500; letter-spacing: 2px; text-transform: uppercase;
  }
  .name-sep {
    width: 3px; height: 30px; background: var(--white); margin: 0 22px;
  }
  .person-title {
    font-size: 20px; letter-spacing: 2px; text-transform: uppercase;
  }
  .contacts {
    position: absolute; left: 0; top: 262px; width: 100%; height: 160px;
    display: flex;
  }
  .contact {
    flex: 1; display: flex; flex-direction: column; align-items: center;
    justify-content: flex-start; padding-top: 14px; gap: 22px;
    position: relative;
  }
  .contact + .contact::before {
    content: ""; position: absolute; left: 0; top: 6px;
    width: 3px; height: 140px; background: var(--divider);
  }
  .contact-icon {
    width: 70px; height: 70px; border-radius: 50%;
    background: radial-gradient(circle at 40% 35%, var(--icon-light), var(--blue-deep) 75%);
    display: flex; align-items: center; justify-content: center;
  }
  .contact-icon svg { width: 38px; height: 38px; }
  .contact-text {
    font-size: 25px; color: var(--ink); letter-spacing: 1px;
  }
  .address-strip {
    position: absolute; left: 0; top: 440px; width: 100%; height: 44px;
    background: linear-gradient(90deg, var(--blue-deep), var(--blue) 40%, var(--cyan));
    display: flex; align-items: center; padding-left: 40px; gap: 14px;
    color: var(--white);
  }
  .address-strip svg { width: 22px; height: 26px; }
  .address-text { font-size: 20px; letter-spacing: 2px; }
</style>
</head>
<body>
  <section class="card">
    <div class="brand">
      <span class="brand-mark"></span>
      <span class="brand-name">Velmont Realtors</span>
    </div>

    <div class="name-band">
      <svg class="person-icon" viewBox="0 0 46 46" aria-hidden="true">
        <circle cx="23" cy="15" r="10" fill="#ffffff"/>
        <path d="M4 44c0-11 8-17 19-17s19 6 19 17z" fill="#ffffff"/>
      </svg>
      <span class="person-name">Gregory Velmont</span>
      <span class="name-sep"></span>
      <span class="person-title">General Manager</span>
    </div>

    <div class="contacts">
      <div class="contact">
        <span class="contact-icon">
          <svg viewBox="0 0 38 38" aria-hidden="true">
            <rect x="11" y="3" width="16" height="32" rx="3" fill="none" stroke="#fff" stroke-width="2.5"/>
            <rect x="14" y="8" width="10" height="19" fill="#fff"/>
            <circle cx="19" cy="31" r="1.6" fill="#fff"/>
          </svg>
        </span>
        <span class="contact-text">012 555 0148</span>
      </div>
      <div class="contact">
        <span class="contact-icon">
          <svg viewBox="0 0 38 38" aria-hidden="true">
            <rect x="4" y="9" width="30" height="20" fill="none" stroke="#fff" stroke-width="2.5"/>
            <path d="M4 9l15 12 15-12" fill="none" stroke="#fff" stroke-width="2.5"/>
          </svg>
        </span>
        <span class="contact-text">info@velmont.com</span>
      </div>
      <div class="contact">
        <span class="contact-icon">
          <svg viewBox="0 0 38 38" aria-hidden="true" fill="none" stroke="#fff" stroke-width="2">
            <circle cx="19" cy="19" r="14"/>
            <ellipse cx="19" cy="19" rx="6" ry="14"/>
            <path d="M5 19h28M7 12h24M7 26h24M19 5v28"/>
          </svg>
        </span>
        <span class="contact-text">www.velmont.com</span>
      </div>
    </div>

    <div class="address-strip">
      <svg viewBox="0 0 22 26" aria-hidden="true">
        <path d="M11 1a9 9 0 0 0-9 9c0 7 9 15 9 15s9-8 9-15a9 9 0 0 0-9-9z" fill="#fff"/>
        <circle cx="11" cy="10" r="3.5" fill="#2f5fb8"/>
      </svg>
      <span class="address-text">4815 Brindle Ave. #263, La Crescenta, CA 91206</span>
    </div>
  </section>
</body>
</html>
```